Business card design for my company.
I would like the card's background colour to be black. You can also see our web site to get an idea of our brand. https://www.tmwhomecrafting.com.au/
- Name
- Email

```html
<!DOCTYPE html>
<html lang="en">
<head>
<meta charset="utf-8">
<title>TMW Home Crafting – Business Card</title>
<link href="https://fonts.googleapis.com/css2?family=Montserrat:wght@400;500;700&display=swap" rel="stylesheet">
<style>
  :root {
    --stage: #3a3a3a;
    --card: #141414;
    --pattern-a: #1c1c1c;
    --pattern-b: #101010;
    --green: #1a9b4b;
    --white: #ffffff;
  }
  * { margin: 0; padding: 0; box-sizing: border-box; }
  html, body {
    width: 1200px; height: 694px; overflow: hidden;
    background: var(--stage);
    font-family: "Montserrat", Arial, sans-serif;
  }
  .sheet {
    position: relative; width: 1200px; height: 694px;
    display: flex; align-items: center; justify-content: center; gap: 40px;
  }
  .card {
    position: relative; width: 540px; height: 309px;
    border-radius: 22px; background: var(--card);
    box-shadow: 0 14px 30px rgba(0,0,0,.45);
    overflow: hidden;
  }
  .card-front__texture {
    position: absolute; inset: 0;
    background: linear-gradient(125deg, var(--pattern-a) 0%, var(--pattern-b) 60%, var(--pattern-a) 100%);
  }
  .brand {
    position: absolute; display: flex; align-items: center; gap: 10px;
    color: var(--white); font-weight: 700; letter-spacing: .06em;
    text-transform: uppercase; white-space: nowrap; line-height: 1;
  }
  .brand__mark { width: 12px; height: 12px; background: var(--green); flex: none; }
  .card-front .brand { left: 50%; top: 50%; transform: translate(-50%, -50%); font-size: 30px; gap: 12px; }
  .card-front .brand__mark { width: 14px; height: 14px; }
  .card-back .brand { left: 28px; top: 196px; font-size: 15px; }
  .card-back__divider {
    position: absolute; left: 268px; top: 40px; width: 2px; height: 228px;
    background: var(--green);
  }
  .contact { position: absolute; left: 288px; right: 16px; top: 52px; color: var(--white); }
  .contact__name { color: var(--green); font-weight: 700; font-size: 26px; line-height: 1.1; white-space: nowrap; }
  .contact__role { font-size: 14px; font-weight: 500; margin-top: 4px; }
  .contact__list { list-style: none; margin-top: 22px; }
  .contact__item {
    display: flex; align-items: center; gap: 8px;
    font-size: 12px; line-height: 1; margin-bottom: 12px; white-space: nowrap;
  }
  .contact__icon {
    width: 20px; height: 20px; border-radius: 50%; background: var(--green);
    display: flex; align-items: center; justify-content: center; flex: none;
  }
  .contact__icon svg { width: 12px; height: 12px; fill: none; stroke: var(--white); stroke-width: 2; stroke-linecap: round; stroke-linejoin: round; }
</style>
</head>
<body>
<main class="sheet">
  <section class="card card-front">
    <div class="card-front__texture" role="img" aria-label="Embossed chevron line pattern across the dark card face"></div>
    <div class="brand"><span class="brand__mark"></span>TMW Home Crafting</div>
  </section>

  <section class="card card-back">
    <div class="brand"><span class="brand__mark"></span>TMW Home Crafting</div>
    <div class="card-back__divider"></div>
    <div class="contact">
      <p class="contact__name">Liam Fairholt</p>
      <p class="contact__role">General Manager</p>
      <ul class="contact__list">
        <li class="contact__item">
          <span class="contact__icon"><svg viewBox="0 0 24 24"><path d="M12 22s7-7 7-12a7 7 0 0 0-14 0c0 5 7 12 7 12z"/><circle cx="12" cy="10" r="2.5"/></svg></span>
          Northgate, Tasmania, Australia
        </li>
        <li class="contact__item">
          <span class="contact__icon"><svg viewBox="0 0 24 24"><path d="M5 3h4l2 5-3 2a11 11 0 0 0 6 6l2-3 5 2v4a2 2 0 0 1-2 2A17 17 0 0 1 3 5a2 2 0 0 1 2-2z"/></svg></span>
          0412 555 018
        </li>
        <li class="contact__item">
          <span class="contact__icon"><svg viewBox="0 0 24 24"><rect x="3" y="5" width="18" height="14" rx="2"/><path d="M3 7l9 6 9-6"/></svg></span>
          info@tmwhomecrafting.com.au
        </li>
        <li class="contact__item">
          <span class="contact__icon"><svg viewBox="0 0 24 24"><circle cx="12" cy="12" r="9"/><path d="M3 12h18M12 3a14 14 0 0 1 0 18M12 3a14 14 0 0 0 0 18"/></svg></span>
          www.tmwhomecrafting.com.au
        </li>
      </ul>
    </div>
  </section>
</main>
</body>
</html>
```